Business card por a urban DJ, up scale audience target

Need a sober design, modern, conservative colors but i can consider some options, y play rnb, hip hop, EDM and top40.

Business card for contact and personal info, double sided, use logo attrached please; im 42 so i need a card acording to my age an target audience.

Target Market(s)

Adult people, up scale audience

Industry/Entity Type

Music Download

Contact Information for Business Card

Cel (318) 4207265518 www.lumadrift.com

Requirements
Must have
• open mind
Nice to have
• open mind
Should not have
• DJ

```html
<!DOCTYPE html>
<html lang="en">
<head>
<meta charset="utf-8">
<title>Luma Drift — Business Card</title>
<link rel="stylesheet" href="https://fonts.googleapis.com/css2?family=Jost:wght@400;500;700;800&display=swap">
<style>
  :root {
    --canvas: #d9d6d1;
    --card-white: #ffffff;
    --card-black: #141414;
    --band-top: #2a2a2a;
    --ink: #1a1a1a;
    --paper-text: #f4f4f4;
    --muted: #bdbdbd;
    --shadow: rgba(0,0,0,0.28);
  }
  * { box-sizing: border-box; margin: 0; padding: 0; }
  html, body {
    width: 1200px; height: 950px; overflow: hidden;
    background: var(--canvas);
    font-family: "Jost", "Futura", sans-serif;
  }
  .sheet {
    width: 1200px; height: 950px;
    display: flex; flex-direction: column;
    align-items: center; justify-content: center; gap: 50px;
  }
  .card {
    width: 700px; height: 400px;
    border-radius: 4px; overflow: hidden;
    box-shadow: 0 14px 30px var(--shadow);
    position: relative;
  }
  /* Front */
  .card--front { background: var(--card-white); display: flex; flex-direction: column; }
  .front__brand {
    flex: 0 0 62%;
    display: flex; align-items: center; justify-content: center; gap: 18px;
  }
  .brand-mark { width: 34px; height: 34px; background: var(--ink); }
  .brand-name {
    font-weight: 800; font-size: 96px; letter-spacing: 4px;
    color: var(--ink); line-height: 1;
  }
  .front__band {
    flex: 1;
    background: linear-gradient(180deg, var(--band-top) 0%, var(--card-black) 55%);
    color: var(--paper-text);
    display: flex; align-items: center; justify-content: space-between;
    padding: 0 56px;
  }
  .identity { display: flex; align-items: center; gap: 16px; }
  .person__name { font-weight: 500; font-size: 30px; letter-spacing: 1px; line-height: 1.05; }
  .person__title { font-weight: 500; font-size: 19px; letter-spacing: 1px; color: var(--muted); }
  .contacts { list-style: none; display: flex; flex-direction: column; gap: 14px; }
  .contact { display: flex; align-items: center; gap: 14px; font-size: 21px; letter-spacing: 0.5px; }
  .icon { width: 26px; height: 26px; flex: 0 0 26px; }
  /* Back */
  .card--back {
    background: var(--card-black); color: var(--paper-text);
    display: flex; align-items: flex-end; padding: 0 0 64px 64px;
  }
  .card--back .contacts { gap: 16px; }
  .card--back .contact { font-size: 24px; }
</style>
</head>
<body>
<main class="sheet">

  <section class="card card--front" aria-label="Card front">
    <div class="front__brand">
      <span class="brand-mark" aria-hidden="true"></span>
      <span class="brand-name">LUMA</span>
    </div>
    <div class="front__band">
      <div class="identity">
        <svg class="icon" viewBox="0 0 26 26" aria-hidden="true">
          <circle cx="13" cy="13" r="13" fill="#f4f4f4"/>
          <circle cx="13" cy="10" r="4" fill="#141414"/>
          <path d="M6 20c1.5-4 4-5 7-5s5.5 1 7 5z" fill="#141414"/>
        </svg>
        <div class="person">
          <p class="person__name">MARCUS VALE</p>
          <p class="person__title">CEO/FOUNDER</p>
        </div>
      </div>
      <ul class="contacts">
        <li class="contact">
          <svg class="icon" viewBox="0 0 26 26" aria-hidden="true">
            <circle cx="13" cy="13" r="13" fill="#f4f4f4"/>
            <rect x="9" y="6" width="8" height="14" rx="1.5" fill="#141414"/>
            <rect x="10.5" y="8" width="5" height="8" fill="#f4f4f4"/>
          </svg>
          <span>(318) 4207265518</span>
        </li>
        <li class="contact">
          <svg class="icon" viewBox="0 0 26 26" aria-hidden="true">
            <circle cx="13" cy="13" r="13" fill="#f4f4f4"/>
            <circle cx="13" cy="13" r="7" fill="none" stroke="#141414" stroke-width="1.6"/>
            <ellipse cx="13" cy="13" rx="3" ry="7" fill="none" stroke="#141414" stroke-width="1.4"/>
            <line x1="6" y1="13" x2="20" y2="13" stroke="#141414" stroke-width="1.4"/>
          </svg>
          <span>www.lumadrift.com</span>
        </li>
      </ul>
    </div>
  </section>

  <section class="card card--back" aria-label="Card back">
    <ul class="contacts">
      <li class="contact"><span>(318) 4207265518</span></li>
      <li class="contact"><span>www.lumadrift.com</span></li>
    </ul>
  </section>

</main>
</body>
</html>
```